A Label for an ECO Friendly Spirit Company

Design a label which can be used for vodka and gin (London Dry Gin). It should be Square type Like the Shape File you see in the uploads. KIRO means Kind Inventive Rare and Original. We want a cool and slim label that calls for eco-friendly. We want to use it for our premium
Vodka and our London Dry Gin. Please use the logo and design it in Square Type.

40%vol, 700ml

Target Market(s)

spirits and events

Industry/Entity Type

SPIRITS

Colors
00AB8E
00BBA5
67D7C9
C6EFE9
E9F9F6
59FF00
82FF00
B8FF75
E3FFCB
F4FFEA

Requirements
Must have
• Logo from KIRO, Squaee Shape

```html
<!DOCTYPE html>
<html lang="en">
<head>
<meta charset="utf-8">
<title>KIRO Vodka Label</title>
<link rel="stylesheet" href="https://fonts.googleapis.com/css2?family=Montserrat:wght@500;600&family=Yellowtail&family=Roboto+Condensed:ital,wght@1,500&display=swap">
<style>
  :root {
    --teal-deep: #00AB8E;
    --teal: #00BBA5;
    --teal-light: #67D7C9;
    --mint: #C6EFE9;
    --mint-pale: #E9F9F6;
    --white: #FFFFFF;
    --bg-top: #E8ECF4;
    --bg-bottom: #D9E0EC;
  }
  * { margin: 0; padding: 0; box-sizing: border-box; }
  html, body { width: 1200px; height: 800px; overflow: hidden; }
  body {
    background: linear-gradient(180deg, var(--bg-top), var(--bg-bottom));
    font-family: "Montserrat", sans-serif;
    position: relative;
  }
  .brand-lockup {
    position: absolute;
    top: 78px; left: 0; width: 1200px;
    display: flex; justify-content: center; align-items: center; gap: 14px;
  }
  .brand-square {
    width: 52px; height: 52px; border-radius: 8px;
    background: var(--teal-deep);
  }
  .brand-name {
    font-weight: 600; font-size: 54px; line-height: 1;
    color: var(--teal-deep); letter-spacing: 1px;
  }
  .label {
    position: absolute;
    left: 387px; top: 250px; width: 426px; height: 426px;
  }
  .label svg { position: absolute; inset: 0; }
  .label-text {
    position: absolute; inset: 0;
    color: var(--white); text-align: center;
  }
  .label-text > * { position: absolute; left: 0; width: 100%; }
  .crest-emblem {
    left: 175px !important; width: 76px !important; top: 64px; height: 68px;
    border-radius: 50% / 46%;
    background: radial-gradient(circle, var(--mint-pale) 0 34%, rgba(255,255,255,0.18) 36%);
    border: 2px solid var(--white);
  }
  .brand-title {
    top: 150px; font-weight: 500; font-size: 30px; line-height: 1;
    display: flex; justify-content: center; align-items: center; gap: 12px;
  }
  .brand-title::before, .brand-title::after {
    content: ""; width: 62px; height: 1px; background: var(--white);
  }
  .product-name {
    top: 184px; font-weight: 500; font-size: 46px; line-height: 1;
    letter-spacing: 14px; padding-left: 14px;
  }
  .grade {
    top: 236px; font-family: "Yellowtail", "Brush Script MT", cursive; font-size: 22px; line-height: 1;
    display: flex; justify-content: center; align-items: center; gap: 10px;
  }
  .grade::before, .grade::after {
    content: ""; width: 72px; height: 1px; background: var(--mint);
  }
  .tagline-top {
    top: 263px; font-size: 11px; font-weight: 500; letter-spacing: 0.3px;
  }
  .tagline-bottom {
    top: 282px; font-size: 9.5px; font-weight: 600; letter-spacing: 4.5px; padding-left: 4.5px;
  }
  .spec-pill {
    top: 303px; left: 144px !important; width: 138px !important; height: 20px;
    border: 1px solid var(--white); border-radius: 10px;
    display: flex; justify-content: space-around; align-items: center;
    font-family: "Roboto Condensed", sans-serif; font-style: italic; font-weight: 500; font-size: 13px;
  }
</style>
</head>
<body>
  <div class="brand-lockup">
    <div class="brand-square"></div>
    <div class="brand-name">KIRO</div>
  </div>

  <div class="label">
    <svg width="426" height="426" viewBox="0 0 426 426">
      <defs>
        <linearGradient id="label-sheen" x1="0" y1="0" x2="1" y2="1">
          <stop offset="0" stop-color="#00AB8E"/>
          <stop offset="0.35" stop-color="#00BBA5"/>
          <stop offset="0.5" stop-color="#67D7C9"/>
          <stop offset="0.65" stop-color="#00BBA5"/>
          <stop offset="1" stop-color="#00AB8E"/>
        </linearGradient>
      </defs>
      <polygon class="label-body" points="213,0 426,213 213,426 0,213" fill="url(#label-sheen)"/>
      <polygon class="label-frame-outer" points="213,6 420,213 213,420 6,213" fill="none" stroke="#FFFFFF" stroke-width="2"/>
      <polygon class="label-frame-inner" points="213,12 414,213 213,414 12,213" fill="none" stroke="#FFFFFF" stroke-width="0.8"/>
      <g class="corner-ornaments" fill="#C6EFE9" opacity="0.55">
        <rect role="img" aria-label="Interlaced key-pattern corner ornament" x="199" y="24" width="28" height="28" transform="rotate(45 213 38)"/>
        <rect role="img" aria-label="Interlaced key-pattern corner ornament" x="24" y="199" width="28" height="28" transform="rotate(45 38 213)"/>
        <rect role="img" aria-label="Interlaced key-pattern corner ornament" x="374" y="199" width="28" height="28" transform="rotate(45 388 213)"/>
        <rect role="img" aria-label="Interlaced key-pattern corner ornament" x="199" y="374" width="28" height="28" transform="rotate(45 213 388)"/>
      </g>
    </svg>
    <div class="label-text">
      <div class="crest-emblem" role="img" aria-label="Crowned crest ornament framing the brand emblem"></div>
      <div class="brand-title">KIRO</div>
      <div class="product-name">VODKA</div>
      <div class="grade">Premium</div>
      <div class="tagline-top">KIND INVENTIVE</div>
      <div class="tagline-bottom">RARE AND ORIGINAL</div>
      <div class="spec-pill"><span>40%vol</span><span>700ml</span></div>
    </div>
  </div>
</body>
</html>
```